Business Card for Polygraph business in Africa

Business Card . Polygraph Examiner based in Tanzania, East Africa.
Business Card will be used to disseminate contact information to potential clients.
It should convey that I am a professional specifically in the polygraph field and perform my work with integrity.

I have attached the business card that I'm currently using, which I threw together myself initially. It's not professional enough.

Target Market(s)

Banks, Accounting Firms, Government Ministries, Gas, Oil, & Gemstone Mining Concerns, Wildlife Conservation NGOs, International companies located in East Africa.

Industry/Entity Type

Business

Contact Information for Business Card

Veritrace Kilonga
Miriam Holloway
PO Box 48317
Arusha, Tanzania
+255 612 839 274
miriamholloway@postvale.example

Colors
00a990
f37122
faa54b

Requirements
Must have
• - Veritrace Kilonga (with the word "Polygraph" being more prominent than the word "Tanzania")
• - Forensic Examinations
• - Employment Screening
• - Should contain a logo of the Continental Truthline Society (of which I'm a member)
• - I would like an accent design (such as the polygraph "squiggles" of a cardio tracing or such as that)
• - My contact information (less prominent, but large enough to read legibly). I would also consider putting the contact information on the second side of the card.
Nice to have
• My color suggestions are changeable.
Should not have
• Anything "cutesy" or "cartoonish"

```html
<!DOCTYPE html>
<html lang="en">
<head>
<meta charset="utf-8">
<title>Veritrace Kilonga – Business Card</title>
<link rel="stylesheet" href="https://fonts.googleapis.com/css2?family=Roboto:wght@300;400;700&display=swap">
<style>
  :root {
    --page-bg: #e8e6e3;
    --card-white: #f4f4f4;
    --brand-blue: #02468f;
    --name-blue: #0b4b97;
    --text-grey: #454545;
    --sub-grey: #5a5a5a;
    --seal-ring: #2b3a8f;
    --white: #ffffff;
  }
  * { box-sizing: border-box; margin: 0; padding: 0; }
  html, body {
    width: 1200px; height: 960px; overflow: hidden;
    background: var(--page-bg);
    font-family: "Roboto", Arial, sans-serif;
  }
  .canvas { position: relative; width: 1200px; height: 960px; }

  .card {
    position: absolute; width: 600px; height: 343px;
    box-shadow: 0 3px 6px rgba(0,0,0,0.25);
  }
  .card--front { left: 314px; top: 113px; background: var(--card-white); }
  .card--back  { left: 311px; top: 472px; background: var(--brand-blue); }

  .brand-name {
    position: absolute; left: 53px; top: 66px;
    font-weight: 700; font-size: 34px; letter-spacing: 0.5px;
    color: var(--brand-blue);
  }

  .member-seal {
    position: absolute; left: 514px; top: 17px;
    width: 70px; height: 70px; border-radius: 50%;
    background: var(--white);
    border: 3px solid var(--seal-ring);
  }

  .contact {
    position: absolute; left: 52px; top: 198px;
    color: var(--text-grey); font-size: 14.5px; line-height: 19px;
  }
  .contact__address { margin-bottom: 8px; }
  .contact__line { display: flex; align-items: center; gap: 7px; }
  .contact__line svg { width: 13px; height: 13px; fill: var(--brand-blue); flex: none; }

  .holder {
    position: absolute; right: 52px; top: 227px; text-align: right;
  }
  .holder__name {
    font-weight: 700; font-size: 21px; color: var(--name-blue); letter-spacing: 0.3px;
  }
  .holder__company {
    margin-top: 2px; font-weight: 300; font-size: 15px;
    color: var(--sub-grey); letter-spacing: 1px;
  }

  .back-name {
    position: absolute; left: 0; right: 0; top: 146px; text-align: center;
    font-weight: 700; font-size: 38px; color: var(--white); letter-spacing: 0.5px;
  }
  .services {
    position: absolute; left: 0; right: 0; top: 287px;
    display: flex; justify-content: center; align-items: center; gap: 9px;
    color: var(--white); font-size: 14.5px;
  }
  .services__dot { width: 6px; height: 6px; border-radius: 50%; background: var(--white); }
</style>
</head>
<body>
<main class="canvas">
  <section class="card card--front" aria-label="Card front">
    <div class="brand-name">Veritrace Kilonga</div>
    <div class="member-seal" role="img" aria-label="Continental Truthline Society membership seal"></div>

    <div class="contact">
      <p class="contact__address">PO Box 48317<br>Arusha, Tanzania</p>
      <p class="contact__line">
        <svg viewBox="0 0 24 24" aria-hidden="true"><path d="M6.6 10.8a15.1 15.1 0 0 0 6.6 6.6l2.2-2.2a1 1 0 0 1 1-.25 11.4 11.4 0 0 0 3.6.57 1 1 0 0 1 1 1V20a1 1 0 0 1-1 1A17 17 0 0 1 3 4a1 1 0 0 1 1-1h3.5a1 1 0 0 1 1 1c0 1.25.2 2.45.57 3.57a1 1 0 0 1-.25 1z"/></svg>
        +255 612 839 274
      </p>
      <p class="contact__line">
        <svg viewBox="0 0 24 24" aria-hidden="true"><path d="M2 5h20v14H2z M2 5l10 8 10-8" fill="none" stroke="#02468f" stroke-width="2.4"/></svg>
        miriamholloway@postvale.example
      </p>
      <p class="contact__line">
        <svg viewBox="0 0 24 24" aria-hidden="true"><circle cx="12" cy="12" r="10"/><path d="M2 12h20M12 2c3 3 3 17 0 20M12 2c-3 3-3 17 0 20" fill="none" stroke="#f4f4f4" stroke-width="1.6"/></svg>
        www.miriamholloway.example
      </p>
    </div>

    <div class="holder">
      <p class="holder__name">MIRIAM HOLLOWAY</p>
      <p class="holder__company">VERITRACE KILONGA</p>
    </div>
  </section>

  <section class="card card--back" aria-label="Card back">
    <div class="back-name">Veritrace Kilonga</div>
    <p class="services">
      <span>Forensic Examinations</span>
      <span class="services__dot"></span>
      <span>Employment Screening</span>
    </p>
  </section>
</main>
</body>
</html>
```